Vietnam Motorcycle Trip TRAVEL GUIDE!! Book Cover!

I need an adventurous book cover for a book called "THROTTLE MERIDIAN: A Wanderer's Manual for Crossing the Breadth of Vietnam". I would like people to look at the cover and think adventure and Vietnam. I want it to appeal to backpackers and people who have not travelled to Vietnam. A motorbike riding along a road in Vietnam would be ideal with some landscapes to suggest we are definitely in Vietnam. The rear cover could perhaps be one of Vietnam's tropical beaches or something else that says "this place is a paradise". It could also be something else that is quinessentially Vietnamese.

The book will be A5 Dimensions. And it will also need a printable A5 interior cover too. The interior covers can just be images. No text needed. These interior images can be motorcycle related or Vietnam related. Perhaps some images of Vietnam or some Pho or Banh Mi to give it a bit of flavour. Or a long open road with a motorbike on it.

Please leave space in the external rear, lower right hand corner for a barcode.

I've attached some images to gain inspiration from. And a sample chapter.

Colours I'd like to see on there - greens, camoflague perhaps, yellow, brown, blue.

Target Market(s)

Male backpackers aged 18-35 years old. New Zealand and Australian travellers.

Font styles to use
Serif
Sans Serif

Requirements
Must have
• Exterior and Interior covers.
Barcode space.
Title and subtitle.
Synopsis on rear cover.
Exciting title fonts - perhaps Brushstroke or something equally exciting and rugged
Nice to have
• Colours I'd like to see on there - greens, camoflague perhaps, yellow, brown, blue.

A motorbike riding on the open road of Vietnam.

Rice paddies, beaches, Korvan Conflict stuff perhaps.

A New Zealand Flag
A Vietnam Flag
Should not have
• Scenery from countries outside Southeast Asia

```html
<!DOCTYPE html>
<html lang="en">
<head>
<meta charset="utf-8">
<title>Throttle Meridian – Cover Spread</title>
<link href="https://fonts.googleapis.com/css2?family=Permanent+Marker&family=Oswald:wght@500;600;700&family=Lato:wght@400;700;900&display=swap" rel="stylesheet">
<style>
  :root{
    --stage:#2b2b2b;
    --yellow:#f6e21e;
    --yellow-deep:#ead012;
    --blue:#1565c0;
    --ink:#111111;
    --spine:#2a2b2d;
    --olive:#8a7f44;
    --haze:#c8c626;
    --leaf:#6f9a2c;
    --jungle:#2f6a2c;
    --jungle-dark:#1d3f22;
    --road:#4d6660;
    --white:#ffffff;
  }
  *{margin:0;padding:0;box-sizing:border-box}
  html,body{width:850px;height:1200px;overflow:hidden;background:var(--stage)}
  .canvas{position:relative;width:850px;height:1200px;background:var(--stage)}
  .spread{position:absolute;left:30px;top:331px;width:791px;height:537px;display:flex}

  /* back cover */
  .back-cover{position:relative;width:375px;height:537px;overflow:hidden;
    background:radial-gradient(ellipse at 50% 30%,var(--yellow) 0%,var(--yellow-deep) 85%)}
  .back-photo{position:absolute;left:0;bottom:0;width:375px;height:190px;
    background:
      radial-gradient(ellipse at 65% 70%,rgba(40,60,55,.55) 0%,rgba(40,60,55,0) 55%),
      linear-gradient(180deg,rgba(234,208,18,0) 0%,var(--leaf) 14%,var(--jungle) 32%,var(--road) 62%,var(--jungle-dark) 100%)}
  .back-headline{position:absolute;left:23px;top:18px;width:340px;
    font-family:"Lato",sans-serif;font-weight:400;font-size:18.5px;line-height:24px;color:var(--ink)}
  .back-headline strong{font-weight:900;color:var(--blue)}
  .blurb{position:absolute;left:23px;width:334px;font-family:"Lato",sans-serif;font-size:7.3px;line-height:9.4px;color:var(--ink)}
  .blurb-intro{top:75px}
  .blurb-author{top:121px}
  .reveals-title{position:absolute;left:23px;top:151px;font-family:"Lato",sans-serif;font-weight:700;
    font-size:9px;color:var(--blue);text-transform:uppercase}
  .reveals-list{position:absolute;left:23px;top:168px;width:334px;list-style:none;
    font-family:"Lato",sans-serif;font-weight:700;font-size:8.4px;line-height:9.5px;color:var(--ink)}
  .reveals-list li{position:relative;padding-left:15px;margin-bottom:8.4px}
  .reveals-list li::before{content:"";position:absolute;left:3px;top:3.5px;width:3.5px;height:3.5px;border-radius:50%;background:var(--ink)}
  .blurb-closing{top:307px}
  .tagline{position:absolute;left:23px;top:334px;font-family:"Permanent Marker",cursive;
    font-size:25px;line-height:1;color:var(--ink);white-space:nowrap;
    transform:scaleX(.84);transform-origin:left center}
  .flags{position:absolute;left:240px;top:401px;display:flex;gap:2px}
  .flag{width:33px;height:19px}
  .flag-vn{background:#d8261f}
  .flag-nz{background:#1d2f7a}
  .site-name{position:absolute;left:240px;top:423px;font-family:"Lato",sans-serif;font-weight:700;
    font-size:8.5px;letter-spacing:.6px;color:var(--white)}
  .site-note{position:absolute;left:240px;top:437px;font-family:"Lato",sans-serif;font-size:5.5px;
    letter-spacing:.4px;color:rgba(255,255,255,.7)}
  .barcode-area{position:absolute;left:240px;top:450px;width:111px;height:66px;background:var(--white);
    display:flex;align-items:center;justify-content:center;
    font-family:Georgia,serif;font-size:5px;letter-spacing:2px;color:#333}

  /* spine */
  .spine{position:relative;width:37px;height:537px;margin-left:3px;background:var(--spine)}
  .spine-title{position:absolute;left:50%;top:22px;transform:translateX(-50%);writing-mode:vertical-rl;
    font-family:"Permanent Marker",cursive;font-size:16px;letter-spacing:1.5px;color:var(--white);white-space:nowrap}
  .spine-subtitle{position:absolute;left:50%;top:298px;transform:translateX(-50%);writing-mode:vertical-rl;
    font-family:"Oswald",sans-serif;font-weight:600;font-size:6.6px;letter-spacing:.7px;color:var(--white);white-space:nowrap}

  /* front cover */
  .front-cover{position:relative;width:375px;height:537px;margin-left:1px;overflow:hidden;
    background:radial-gradient(ellipse at 50% 25%,var(--yellow) 0%,var(--yellow-deep) 75%)}
  .front-photo{position:absolute;left:0;top:215px;width:375px;height:322px;
    background:
      radial-gradient(ellipse at 35% 35%,rgba(200,198,38,.55) 0%,rgba(200,198,38,0) 45%),
      linear-gradient(180deg,rgba(234,208,18,0) 0%,var(--haze) 14%,var(--leaf) 34%,var(--jungle) 56%,var(--jungle-dark) 76%,var(--road) 100%)}
  .title{position:absolute;left:0;width:375px;text-align:center;font-family:"Permanent Marker",cursive;line-height:1;white-space:nowrap}
  .title-top{top:16px;font-size:52px;color:var(--blue);letter-spacing:2px}
  .title-bottom{top:74px;font-size:46px;color:var(--ink);letter-spacing:8px}
  .subtitle-band{position:absolute;left:25px;top:133px;width:339px;height:87px}
  .subtitle{position:absolute;left:25px;top:152px;width:339px;text-align:center;
    font-family:"Oswald",sans-serif;font-weight:600;font-size:18px;line-height:21.5px;color:var(--white);
    transform:skewX(-10deg)}
  .author{position:absolute;left:0;top:494px;width:375px;text-align:center;
    font-family:"Oswald",sans-serif;font-weight:700;font-size:23px;line-height:30px;letter-spacing:5px;color:var(--yellow)}
</style>
</head>
<body>
<main class="canvas">
  <div class="spread">

    <section class="back-cover">
      <div class="back-photo" role="img" aria-label="Photo of two riders on a scooter on a winding mountain road, one waving, green hills behind"></div>

      <h2 class="back-headline"><strong>TRAVEL LIKE A PRO</strong> IN A COUNTRY<br>WHERE BRIBING COPS IS <strong>NORMAL!</strong></h2>

      <p class="blurb blurb-intro">Everyone knows someone who’s ridden the breadth of Vietnam. What if you could do the same? For us Kiwis and Australians, it’s difficult finding decent material about motorcycling in Vietnam. With so much conflicting information online and uncertainty around costs, it’s no wonder people keep putting off this 1600 km road trip.</p>

      <p class="blurb blurb-author">Callum Ashridge has been there and done it. In the flesh. And whether your goal is riding from Saigon to Hanoi or between beach towns, this guide is your bulletproof vest.</p>

      <h3 class="reveals-title">This step-by-step wanderer’s manual reveals:</h3>
      <ul class="reveals-list">
        <li>How to plan your own motorcycle journey before leaving home</li>
        <li>Where and how to buy/rent a bike</li>
        <li>What types of licences and insurance you’ll need</li>
        <li>How to finish your trip alive without being run over by a pig truck</li>
        <li>How to avoid getting shaken down by dodgy cops</li>
        <li>Itemized expense reports, showing this journey is possible for as little as NZ$90 per day and even as low as $50.</li>
        <li>A day-by-day riding itinerary</li>
      </ul>

      <p class="blurb blurb-closing">Let’s face it. None of us are getting any younger. Your own Vietnam motorcycle journey awaits. And with all the information you need in one lightweight book, what’s stopping you?</p>

      <p class="tagline">THIS PLACE IS A PARADISE!</p>

      <div class="flags">
        <span class="flag flag-vn"></span>
        <span class="flag flag-nz"></span>
      </div>
      <p class="site-name">meridianroads.net</p>
      <p class="site-note">TRAVEL GUIDE</p>
      <div class="barcode-area">BARCODE AREA</div>
    </section>

    <section class="spine">
      <p class="spine-title">THROTTLE MERIDIAN</p>
      <p class="spine-subtitle">A WANDERER’S MANUAL FOR CROSSING THE BREADTH OF VIETNAM</p>
    </section>

    <section class="front-cover">
      <div class="front-photo" role="img" aria-label="Photo of karst limestone mountains and green fields with two motorbikes on a long open road"></div>

      <h1>
        <span class="title title-top">THROTTLE</span>
        <span class="title title-bottom">MERIDIAN</span>
      </h1>

      <svg class="subtitle-band" viewBox="0 0 339 87" aria-hidden="true">
        <path fill="var(--olive)" d="M14 7 L60 3 L70 6 L150 2 L250 4 L300 1 L326 8 L312 13 L337 20 L320 28 L334 38 L316 46 L332 56 L318 64 L330 74 L305 80 L240 84 L150 82 L60 86 L12 84 L26 76 L2 68 L18 60 L4 50 L22 42 L3 32 L20 24 L6 15 Z"/>
      </svg>
      <p class="subtitle">A WANDERER’S MANUAL<br>FOR CROSSING THE<br>BREADTH OF VIETNAM</p>

      <p class="author">CALLUM ASHRIDGE</p>
    </section>

  </div>
</main>
</body>
</html>
```